Environmental Plastics Infographic on Marine Debris

We need a series of infographics that can be used individually or as a combined presentation. We'd like the combined piece to include an introduction and conclusion along with 4-5 infographics. Each infographic (information unit) should also work as a standalone. We are trying to help people visualize size proportions and ratios to put the plastics marine debris problem in perspective. Our key point is concerning polystyrene foam which represents 35 tons. We are looking for something creative to help people understand what the problem represents in terms they are familiar with.

To view our typical company design/style please see our website at www.harbenfieldgroup.org. Our primary RGB colors are: (187,140,9); (94,47,29); (94,138,164); and (164,167,15). Secondary RGB colors are (249,162,28) and (218,210,208). Our title/header font is DIN Next LT Pro and our copy font is Calibri 10.5 pt. We can deviate from the font specification if beneficial and welcome interesting text treatments and typography.

Need extra days to review

Target Market(s)

international brand manufacturers (brightmoor, kavo), US legislators & government agencies

Font styles to use
Sans Serif

Requirements
Must have
• Sufficient white space. Easy to grasp message concept with visual components.

```html
<!DOCTYPE html>
<html lang="en">
<head>
<meta charset="utf-8">
<title>How Big is BIG?</title>
<link href="https://fonts.googleapis.com/css2?family=Open+Sans:wght@300;400;700;800&display=swap" rel="stylesheet">
<style>
  :root {
    --bg: #dbd3d2;
    --column: #b9afad;
    --column-edge: #aaa09f;
    --label-band: #e3dfdf;
    --title: #0f2d3a;
    --label: #e8731a;
    --figure: #e04e0a;
    --unit: #ec7b2c;
    --blue-light: #6392ad;
    --blue-dark: #24566f;
    --wave-pale: #a3b1ba;
  }
  * { margin: 0; padding: 0; box-sizing: border-box; }
  html, body { width: 1200px; height: 899px; overflow: hidden; background: var(--bg); }
  .canvas {
    position: relative; width: 1200px; height: 899px; overflow: hidden;
    background: var(--bg); font-family: "Open Sans", Arial, sans-serif;
  }
  .headline {
    position: absolute; top: 74px; left: 0; width: 100%;
    text-align: center; color: var(--title);
    font-weight: 700; font-size: 74px; letter-spacing: -0.5px; line-height: 1;
  }
  .comparison {
    position: absolute; top: 202px; bottom: 0; width: 285px;
    background: var(--column);
  }
  .comparison--ship { left: 154px; }
  .comparison--whale { left: 458px; }
  .comparison--waste { left: 762px; }
  .comparison__art-band {
    position: absolute; top: 0; left: 0; width: 100%; height: 136px;
    border-bottom: 4px solid var(--column-edge);
  }
  .comparison__art {
    position: absolute;
    background: linear-gradient(90deg, var(--blue-light), var(--blue-dark));
  }
  .art--ship { left: 14px; right: 10px; top: 52px; height: 82px; border-radius: 6px 6px 2px 2px; }
  .art--whale { left: -12px; right: -12px; top: 54px; height: 60px; border-radius: 50% 40% 50% 50%; }
  .art--waste { left: 18px; right: 0; top: -42px; height: 176px; border-radius: 2px 2px 0 0;
    background: linear-gradient(90deg, var(--blue-light), var(--blue-dark) 55%); }
  .comparison__label {
    position: absolute; top: 140px; left: 0; width: 100%; height: 98px;
    background: var(--label-band); color: var(--label);
    display: flex; flex-direction: column; align-items: center; justify-content: center;
    text-align: center; font-weight: 700; font-size: 29px; line-height: 1.15;
  }
  .comparison__label small { display: block; font-size: 20.5px; margin-top: 4px; }
  .comparison__stat {
    position: absolute; top: 300px; left: 0; width: 100%; text-align: center; z-index: 3;
  }
  .stat__figure {
    display: block; color: var(--figure); font-weight: 800; font-size: 90px;
    line-height: 1; letter-spacing: -2px;
  }
  .stat__unit {
    display: block; color: var(--unit); font-weight: 300; font-size: 50px;
    line-height: 1; margin-top: -6px;
  }
  .waves { position: absolute; left: 0; top: 0; z-index: 2; pointer-events: none; }
</style>
</head>
<body>
<div class="canvas">
  <h1 class="headline">How Big is BIG?</h1>

  <section class="comparison comparison--ship">
    <div class="comparison__art-band">
      <div class="comparison__art art--ship" role="img" aria-label="Illustration of a cruise ship"></div>
    </div>
    <div class="comparison__label">ONE CRUISE SHIP</div>
    <div class="comparison__stat"><span class="stat__figure">79%</span><span class="stat__unit">GPGP</span></div>
  </section>

  <section class="comparison comparison--whale">
    <div class="comparison__art-band">
      <div class="comparison__art art--whale" role="img" aria-label="Illustration of a blue whale"></div>
    </div>
    <div class="comparison__label">ONE BLUE WHALE</div>
    <div class="comparison__stat"><span class="stat__figure">53%</span><span class="stat__unit">GPGP</span></div>
  </section>

  <section class="comparison comparison--waste">
    <div class="comparison__art-band">
      <div class="comparison__art art--waste" role="img" aria-label="Illustration of a garbage truck in front of the New York City skyline"></div>
    </div>
    <div class="comparison__label">ONE WEEK<small>NYC WASTE GENERATION</small></div>
    <div class="comparison__stat"><span class="stat__figure">29%</span><span class="stat__unit">GPGP</span></div>
  </section>

  <svg class="waves" width="1200" height="899" viewBox="0 0 1200 899" aria-hidden="true">
    <defs>
      <linearGradient id="wave-blue" x1="0" y1="0" x2="1" y2="0">
        <stop offset="0" stop-color="var(--blue-light)"/>
        <stop offset="1" stop-color="var(--blue-dark)"/>
      </linearGradient>
    </defs>
    <path d="M0,415 C120,640 380,790 620,805 C850,815 1050,760 1200,710 L1200,899 L0,899 Z" fill="var(--wave-pale)" opacity="0.7"/>
    <path d="M0,450 C130,690 380,835 620,845 C850,850 1050,790 1200,742 L1200,899 L0,899 Z" fill="url(#wave-blue)" opacity="0.72"/>
  </svg>
</div>
</body>
</html>
```